Oriel Photography Business Card

I need a business card designed for a photography business based in Perth, Western Australia called Oriel Photography.

We specialise in wedding, event photography and portrait photography.

The business card must borrow the style of the attached logo.

The hex codes for the colours in the logo are:
#ED1D85 - Pink
#89C23E - Green
#37282F - Black

The name on the card will be:
Name: Tobrian
Phone: 0417395268
Website: www.orielphotography.example.com.au
Facebook: orielphotography

I am open and happy to accept creative concepts.

I’d like some space at the back for writing notes and appointment details.

```html
<!DOCTYPE html>
<html lang="en">
<head>
<meta charset="utf-8">
<title>Oriel Photography – Business Card</title>
<link rel="stylesheet" href="https://fonts.googleapis.com/css2?family=Open+Sans:wght@300;400;700&display=swap">
<style>
  :root {
    --pink: #ED1D85;
    --green: #89C23E;
    --green-soft: #a3c93f;
    --ink: #37282F;
    --back-bg: #4a3a42;
    --text: #3a3a3a;
    --paper: #ffffff;
    --stage: #e6e6ea;
    --rule: #9a9a9a;
  }
  * { box-sizing: border-box; margin: 0; padding: 0; }
  html, body { width: 1200px; height: 987px; overflow: hidden; }
  body {
    background: var(--stage);
    font-family: "Open Sans", sans-serif;
    position: relative;
  }
  .card {
    position: absolute;
    width: 630px;
    height: 360px;
    border-radius: 26px;
    overflow: hidden;
  }

  /* Front */
  .card-front { left: 60px; top: 480px; background: var(--paper); }
  .card-front .swoosh { position: absolute; inset: 0; }
  .brand {
    position: absolute;
    display: flex;
    align-items: center;
    gap: 22px;
  }
  .brand-name {
    font-weight: 300;
    letter-spacing: 0.5em;
    text-transform: uppercase;
    white-space: nowrap;
  }
  .brand-dot { border-radius: 50%; flex: none; }
  .card-front .brand { left: 60px; top: 34px; }
  .card-front .brand-name { color: var(--text); font-size: 15px; }
  .card-front .brand-dot { width: 58px; height: 58px; background: var(--pink); }

  .contact-list {
    position: absolute;
    left: 60px;
    top: 108px;
    list-style: none;
    color: var(--text);
    font-size: 17px;
    line-height: 30px;
  }
  .contact-list li { display: flex; align-items: center; gap: 10px; }
  .contact-list svg { width: 16px; height: 16px; flex: none; }
  .holder-name {
    position: absolute;
    right: 40px;
    bottom: 24px;
    color: var(--pink);
    font-weight: 700;
    font-size: 28px;
    line-height: 1.2;
    text-transform: uppercase;
    letter-spacing: 0.03em;
  }

  /* Back */
  .card-back { left: 520px; top: 90px; background: var(--back-bg); }
  .notes-panel {
    position: absolute;
    left: 34px;
    top: 70px;
    width: 430px;
    height: 215px;
    background: var(--paper);
    padding: 12px 22px;
  }
  .notes-label { font-size: 18px; color: var(--ink); line-height: 22px; }
  .notes-line { border-bottom: 1px solid var(--rule); height: 30px; }
  .notes-line:first-of-type { margin-top: -4px; margin-left: 60px; height: 8px; }
  .card-back .brand { right: 36px; top: 30px; flex-direction: row-reverse; }
  .card-back .brand-name { color: var(--paper); font-size: 13px; }
  .card-back .brand-dot { width: 50px; height: 50px; background: var(--paper); }
  .card-back .web {
    position: absolute;
    left: 34px;
    bottom: 30px;
    color: var(--paper);
    font-size: 16px;
    letter-spacing: 0.08em;
  }
</style>
</head>
<body>

<section class="card card-front" aria-label="Business card front">
  <svg class="swoosh" viewBox="0 0 630 360" preserveAspectRatio="none" aria-hidden="true">
    <defs>
      <path id="wave" d="M0,56 C5,250 90,275 330,270 C450,268 560,236 630,200 L630,400 L0,400Z"/>
    </defs>
    <use href="#wave" fill="var(--pink)"/>
    <use href="#wave" fill="var(--paper)" transform="translate(0,8)"/>
    <use href="#wave" fill="var(--green-soft)" transform="translate(0,13)"/>
  </svg>

  <div class="brand">
    <span class="brand-name">Oriel Photography</span>
    <span class="brand-dot"></span>
  </div>

  <ul class="contact-list">
    <li>
      <svg viewBox="0 0 16 16" aria-hidden="true"><circle cx="8" cy="8" r="7.5" fill="var(--green)"/><path d="M5.5 4.5l1.3-.3.8 2-1 .7a5 5 0 0 0 2.3 2.3l.7-1 2 .8-.3 1.3c-3.3.3-6.1-2.5-5.8-5.8z" fill="#fff"/></svg>
      0417395268
    </li>
    <li>
      <svg viewBox="0 0 16 16" aria-hidden="true"><rect width="16" height="16" rx="2" fill="var(--green)"/></svg>
      orielphotography
    </li>
    <li>
      <svg viewBox="0 0 16 16" aria-hidden="true"><circle cx="8" cy="8" r="7.5" fill="var(--green)"/><g fill="none" stroke="#fff" stroke-width="1"><ellipse cx="8" cy="8" rx="3" ry="6.5"/><path d="M1.5 8h13M2.5 5h11M2.5 11h11"/></g></svg>
      www.orielphotography.example.com.au
    </li>
  </ul>

  <p class="holder-name">Tobrian</p>
</section>

<section class="card card-back" aria-label="Business card back">
  <div class="notes-panel">
    <p class="notes-label">notes:</p>
    <div class="notes-line"></div>
    <div class="notes-line"></div>
    <div class="notes-line"></div>
    <div class="notes-line"></div>
    <div class="notes-line"></div>
    <div class="notes-line"></div>
  </div>
  <div class="brand">
    <span class="brand-dot"></span>
    <span class="brand-name">Oriel Photography</span>
  </div>
  <p class="web">www.orielphotography.example.com.au</p>
</section>

</body>
</html>
```